Mortgage Company ready to make a statement!

We have a basic logo that I am fairly happy with ... but it could use a little bit of tweaking before we order the sign for our building. We also want some knock-your-socks-off business cards.
Problem: Inside of our Mortgage Office (Bright Fern Mortgage Group), we are going to have a coffee lounge (Sunbrew Cafe) for Realtors to use instead of the local Cuppington to meet with homebuyers. The office and coffee lounge are in an industrial building and is decorated with cozy overstuffed chairs, a hodge podge of interesting lamps and furniture, and goal is to make it as inviting as possible. However, we are a financial institution... so we need to keep it pretty clean as well.
One of my favorite marketing ideas is to cut a house key for everyone who buys a home using us with a key that matches our logo. There's only one key shape that works really well, so that needs to match the logo in order for the idea to work. I'll attach an image of the key blank.... although the way the key hole cut out looks terrible, so I was thinking of having them just do a thin outline instead.
Would like a similar, matching logo for the Sunbrew Cafe... but possibly something that would be a little less formal and would be cute on a coffee mug- nothing stuffy.
AND, we're opening a home inspection company as well, and we would like that logo and branding to match. The home inspection company is "Bright Fern Home Inspections"
We were thinking that for the home inspection company , we could use a magnifying glass shape inside of the house shape for the logo, use a keyhole shape inside of the same house for the mortgage company, and use a coffee cup inside of the house shape for Sunbrew Cafe.
Just getting stuck and need to help. I designed the attached logo myself, and that is what we are currently using. Designers at local printing companies have failed to impress us.
The mortgage industry has a lot of numbers and logos, etc that they require us to put on our business cards... so it's hard to keep them looking clean.
HELP! HELP! :)

```html
<!DOCTYPE html>
<html lang="en">
<head>
<meta charset="utf-8">
<title>Bright Fern Mortgage Group – Business Cards</title>
<link rel="stylesheet" href="https://fonts.googleapis.com/css2?family=Montserrat:wght@500;700&family=Work+Sans:wght@400;500&display=swap">
<style>
  :root {
    --backdrop: #2b2b2e;
    --card: #1b1b1d;
    --accent: #2a6a92;
    --text-light: #f2f2f2;
    --text-muted: #d9d9d9;
  }
  * { margin: 0; padding: 0; box-sizing: border-box; }
  html, body { width: 1200px; height: 900px; overflow: hidden; }
  body {
    background: var(--backdrop);
    font-family: "Work Sans", Arial, sans-serif;
  }
  .canvas {
    position: relative;
    width: 1200px;
    height: 900px;
  }
  .card {
    position: absolute;
    left: 220px;
    width: 760px;
    height: 390px;
    background: var(--card);
    box-shadow: 0 14px 30px rgba(0,0,0,0.55);
    overflow: hidden;
  }
  .card--front { top: 45px; }
  .card--back { top: 465px; }
  .card__band {
    position: absolute;
    left: 0; right: 0; bottom: 0;
    height: 20px;
    background: var(--accent);
  }

  /* Front: wordmark */
  .wordmark {
    position: absolute;
    left: 0; right: 0; top: 150px;
    display: flex;
    align-items: center;
    justify-content: center;
    gap: 18px;
  }
  .wordmark__square {
    width: 26px; height: 26px;
    background: var(--accent);
  }
  .wordmark__name {
    font-family: "Montserrat", Arial, sans-serif;
    font-weight: 500;
    font-size: 38px;
    letter-spacing: 0.5px;
    color: var(--accent);
  }

  /* Back: identity and contacts */
  .identity {
    position: absolute;
    right: 440px;
    top: 120px;
    text-align: right;
  }
  .identity__name {
    font-family: "Montserrat", Arial, sans-serif;
    font-weight: 700;
    font-size: 30px;
    letter-spacing: 1.5px;
    color: var(--text-light);
  }
  .identity__role {
    font-family: "Montserrat", Arial, sans-serif;
    font-weight: 700;
    font-size: 20px;
    letter-spacing: 1px;
    color: var(--text-light);
    margin-top: 6px;
  }
  .divider {
    position: absolute;
    left: 340px;
    top: 118px;
    width: 3px;
    height: 98px;
    background: var(--accent);
  }
  .contacts {
    position: absolute;
    left: 368px;
    top: 120px;
    list-style: none;
  }
  .contacts__item {
    display: flex;
    align-items: center;
    gap: 14px;
    font-size: 19px;
    letter-spacing: 1.5px;
    color: var(--text-muted);
    height: 31px;
  }
  .contacts__icon { width: 16px; height: 16px; flex: none; }
  .address {
    position: absolute;
    left: 0; right: 0;
    bottom: 52px;
    text-align: center;
    font-size: 19px;
    letter-spacing: 2px;
    color: var(--text-muted);
  }
</style>
</head>
<body>
<main class="canvas">
  <section class="card card--front" aria-label="Card front">
    <div class="wordmark">
      <span class="wordmark__square"></span>
      <span class="wordmark__name">Bright Fern Mortgage Group</span>
    </div>
    <div class="card__band"></div>
  </section>

  <section class="card card--back" aria-label="Card back">
    <div class="identity">
      <p class="identity__name">DANA WHITLOW</p>
      <p class="identity__role">CEO</p>
    </div>
    <div class="divider"></div>
    <ul class="contacts">
      <li class="contacts__item">
        <svg class="contacts__icon" viewBox="0 0 16 16" aria-hidden="true">
          <rect x="4" y="1" width="8" height="14" rx="1.5" fill="none" stroke="#f2f2f2" stroke-width="1.5"/>
          <line x1="7" y1="12.5" x2="9" y2="12.5" stroke="#f2f2f2" stroke-width="1.2"/>
        </svg>
        <span>000-555-0142</span>
      </li>
      <li class="contacts__item">
        <svg class="contacts__icon" viewBox="0 0 16 16" aria-hidden="true">
          <rect x="4" y="1" width="8" height="4" fill="#f2f2f2"/>
          <rect x="1" y="5.5" width="14" height="6" rx="1" fill="#f2f2f2"/>
          <rect x="4" y="10" width="8" height="5" fill="#f2f2f2" stroke="#1b1b1d" stroke-width="1"/>
        </svg>
        <span>000-555-0142</span>
      </li>
      <li class="contacts__item">
        <svg class="contacts__icon" viewBox="0 0 16 16" aria-hidden="true">
          <rect x="1" y="3" width="14" height="10" fill="#f2f2f2"/>
          <polyline points="1,3 8,9 15,3" fill="none" stroke="#1b1b1d" stroke-width="1.4"/>
        </svg>
        <span>dana.whitlow@brightfern.com</span>
      </li>
    </ul>
    <p class="address">Lantern Court Sydney Melbourne</p>
    <div class="card__band"></div>
  </section>
</main>
</body>
</html>
```